Finiding oppertunites in Real Estate 6.15.20

size of ad 7” x 9.6”
1-I like the ad to stand out and attract people's attention.
2-you should be able to see the text of the ad clearly .. see the attachment anything in yellow is instructions.
3-the list of topics should not be the main part of the ad
4-if you decide you want a picture or vector of a person .. (you decide)
then it should be a white male about 25-30 years old wearing a solid white or blue shirt and not long hair.
5-leave 1 inch for footer
see attachment
Good luck

Target Market(s)

potential male students 25-35 years of age

Industry/Entity Type

Education

Requirements
Must have
• will stand out and people would want to see it.
should be able to read the words of ad
Nice to have
• how to make money in real estate on one line

```html
<!DOCTYPE html>
<html lang="en">
<head>
<meta charset="utf-8">
<title>Real Estate Career Course Flyer</title>
<link href="https://fonts.googleapis.com/css2?family=Bebas+Neue&family=Oswald:wght@400;500&family=Montserrat:wght@400;500;600;700&display=swap" rel="stylesheet">
<style>
  :root {
    --stage: #e4e4e4;
    --orange: #e5870a;
    --navy: #213a6b;
    --navy-dark: #1a2f58;
    --gold: #f7b515;
    --red: #d9111b;
    --white: #ffffff;
    --ink: #1d1d1f;
    --list-grey: #ececec;
    --photo-light: #cfdff0;
    --photo-mid: #8fb0d6;
  }
  * { margin: 0; padding: 0; box-sizing: border-box; }
  html, body { width: 1200px; height: 613px; overflow: hidden; background: var(--stage); }
  .flyer {
    position: absolute; left: 390px; top: 18px;
    width: 420px; height: 576px;
    background: var(--white);
    overflow: hidden;
    box-shadow: 0 6px 16px rgba(0,0,0,.18);
    font-family: "Montserrat", sans-serif;
  }
  .house { position: absolute; left: 0; top: 0; }
  .header-band { position: absolute; left: 0; top: 0; width: 289px; height: 146px; background: var(--orange); }
  .title {
    position: absolute; left: 19px; top: 28px;
    font-family: "Bebas Neue", sans-serif; font-weight: 400; color: var(--white);
    font-size: 58px; line-height: 52px; letter-spacing: 0;
    transform: scaleX(0.92); transform-origin: left top;
    white-space: nowrap;
  }
  .tagline-band { position: absolute; left: 0; top: 146px; width: 420px; height: 43px; background: var(--navy); }
  .tagline {
    position: absolute; left: 19px; top: 155px;
    font-family: "Oswald", sans-serif; font-size: 17px; color: var(--white); letter-spacing: .1px;
    white-space: nowrap;
  }
  .tagline span { color: var(--gold); font-weight: 500; }
  .photo {
    position: absolute; left: 228px; top: 54px; width: 192px; height: 368px;
    background: radial-gradient(ellipse at 60% 30%, var(--photo-light) 0%, var(--photo-mid) 60%, var(--navy-dark) 100%);
    clip-path: polygon(66px 0, 192px 0, 192px 368px, 0 368px, 0 135px, 66px 135px);
  }
  .audience {
    position: absolute; left: 19px; top: 201px;
    font-size: 12px; line-height: 16.5px; font-weight: 600; color: var(--navy);
  }
  .promise {
    position: absolute; left: 19px; top: 265px;
    font-size: 12.5px; line-height: 14px; color: var(--ink);
  }
  .badge { position: absolute; left: 17px; top: 321px; width: 90px; height: 90px; }
  .badge-text {
    position: absolute; left: 17px; top: 344px; width: 90px; text-align: center;
    font-family: "Bebas Neue", sans-serif; color: var(--white); font-size: 22px; line-height: 20px;
  }
  .date-num {
    position: absolute; font-family: "Bebas Neue", sans-serif; color: var(--red); font-size: 34px; line-height: 30px;
  }
  .date-month {
    position: absolute; font-family: "Bebas Neue", sans-serif; color: var(--red); font-size: 12px; line-height: 12px;
  }
  .date-label {
    position: absolute; left: 148px; width: 86px; padding-left: 8px;
    border-left: 1px solid #d7d7d7;
    background: linear-gradient(90deg, #efefef, rgba(239,239,239,0));
    font-family: "Montserrat", sans-serif; font-weight: 600; font-size: 11.5px; line-height: 12px; color: var(--ink);
  }
  .list-area {
    position: absolute; left: 0; top: 443px; width: 420px; height: 72px;
    background: linear-gradient(90deg, #f6f6f6, var(--list-grey));
  }
  .person-base { position: absolute; left: 0; top: 408px; }
  .topics-heading {
    position: absolute; left: 29px; top: 428px;
    font-size: 9px; font-weight: 700; color: var(--white); letter-spacing: .2px;
  }
  .topics { position: absolute; top: 451px; list-style: none; font-size: 7.6px; font-weight: 500; color: var(--ink); line-height: 12px; }
  .topics li { position: relative; padding-left: 9px; }
  .topics li::before { content: ""; position: absolute; left: 0; top: 4px; width: 3px; height: 3px; border-radius: 50%; background: var(--gold); }
</style>
</head>
<body>
  <main class="flyer">
    <svg class="house" width="420" height="576" viewBox="0 0 420 576" aria-hidden="true">
      <polygon points="274,67 361,7 420,48 420,200 291,200 291,75 282,75" fill="var(--navy)"/>
    </svg>
    <div class="photo" role="img" aria-label="Photo of a smiling young businessman in a light blue shirt and dark tie with arms crossed"></div>
    <div class="header-band"></div>
    <h1 class="title">REAL ESTATE<br>CAREER COURSE</h1>
    <div class="tagline-band"></div>
    <p class="tagline">HOW TO MAKE MONEY IN <span>REAL ESTATE?</span></p>

    <p class="audience">FOR THOSE WHO HAVE STARTED<br>OR WOULD LIKE TO GO INTO<br>REAL ESTATE</p>
    <p class="promise">An investment in knowledge<br>opens up untold opportunities</p>

    <svg class="badge" viewBox="0 0 100 100" aria-hidden="true">
      <polygon fill="var(--red)" points="100,50 91.2,58.2 96.2,69.1 84.9,73.4 85.4,85.4 73.4,84.9 69.1,96.2 58.2,91.2 50,100 41.8,91.2 30.9,96.2 26.6,84.9 14.6,85.4 15.1,73.4 3.8,69.1 8.8,58.2 0,50 8.8,41.8 3.8,30.9 15.1,26.6 14.6,14.6 26.6,15.1 30.9,3.8 41.8,8.8 50,0 58.2,8.8 69.1,3.8 73.4,15.1 85.4,14.6 84.9,26.6 96.2,30.9 91.2,41.8"/>
    </svg>
    <p class="badge-text">REMOTE<br>SESSIONS</p>

    <p class="date-num" style="left:114px; top:334px;">12</p>
    <p class="date-label" style="top:336px;">SESSION<br>COURSE</p>
    <p class="date-num" style="left:115px; top:365px;">16</p>
    <p class="date-month" style="left:115px; top:393px;">JUNE</p>
    <p class="date-label" style="top:371px;">CLASS<br>STARTING</p>

    <div class="list-area"></div>
    <svg class="person-base" width="420" height="36" viewBox="0 0 420 36" aria-hidden="true">
      <polygon points="0,14 194,14 206,0 420,0 420,35 0,35" fill="var(--navy)"/>
    </svg>
    <p class="topics-heading">A PARTIAL LISTING OF TOPICS</p>
    <ul class="topics" style="left:29px;">
      <li>SINGLE-FAMILY</li><li>MULTIFAMILY</li><li>MANAGEMENT</li><li>REAL ESTATE CONCEPTS</li><li>REAL ESTATE LAW</li>
    </ul>
    <ul class="topics" style="left:159px;">
      <li>INVESTMENT PROPERTIES</li><li>FORECLOSURES</li><li>REHAB</li><li>FORECLOSURES</li><li>SHORT SALES</li>
    </ul>
    <ul class="topics" style="left:295px;">
      <li>DEVELOPMENT</li><li>FINICAL MODELING</li><li>HUD PROPERTIES</li><li>DUE DILIGENCE E</li>
    </ul>
  </main>
</body>
</html>
```